Real estate broker business card

Want a modern celan but effective business card for my residential and commercial real estate business. I want the back of the card to advertise my services and to capture business. I have attached the back of my current business card fore ideas
Updates

Logos, photo and text updates added! Added Saturday, September 3, 2016

Project Deadline Extended Reason: LOGOS, PHOTOS AND TEST JUST UPLOADED! I'M READY TO PICK A DESIGN! THANK YOU! Added Saturday, September 3, 2016

Target Market(s)

home buyers and seller. commercial buyers and sellers

Industry/Entity Type

Real Estate

Contact Information for Business Card

must have my contact information and my photo

Requirements
Must have
• Carla Ventrino
• Owner & Qualifying Broker
• Ventrino Real Estate Services
• 505.718.2094
• carla@ventrinohomes.example
• www.ventrinohomes.example
Nice to have
• metallic
• Business capture text: " Don't buy or lease property without someone looking out for your best interests. I will represent you on your home or investment purchase for FREE!"
• "Home owners, call today to receive a FREE market analysis for your homes value!

```html
<!DOCTYPE html>
<html lang="en">
<head>
<meta charset="utf-8">
<title>Ventrino Real Estate Services – Business Card</title>
<link rel="stylesheet" href="https://fonts.googleapis.com/css2?family=Cinzel:wght@400;600&family=Open+Sans:wght@400;600&display=swap">
<style>
  :root {
    --bg: #5f5f5f;
    --teal: #1a8e97;
    --teal-dark: #126d75;
    --teal-light: #2aa9b1;
    --silver: #c9ced1;
    --silver-dark: #8b9296;
    --white: #ffffff;
    --ink-soft: #e9f6f7;
  }
  * { margin: 0; padding: 0; box-sizing: border-box; }
  html, body { width: 1200px; height: 950px; overflow: hidden; }
  body {
    background: var(--bg);
    font-family: "Open Sans", Arial, sans-serif;
    position: relative;
  }
  .card {
    position: absolute;
    left: 250px;
    width: 700px;
    height: 400px;
    overflow: hidden;
    box-shadow: 0 10px 30px rgba(0,0,0,0.35);
  }
  /* Promo side */
  .card-promo { top: 45px; }
  .promo-texture {
    position: absolute; inset: 0;
    background: radial-gradient(ellipse at 50% 50%, var(--teal-light) 0%, var(--teal) 55%, var(--teal-dark) 100%);
  }
  .promo-content {
    position: absolute; inset: 0;
    display: flex; flex-direction: column; align-items: center; justify-content: center;
    color: var(--white); text-align: center;
  }
  .promo-name {
    font-family: "Cinzel", Georgia, serif;
    font-weight: 400;
    font-size: 64px;
    letter-spacing: 3px;
    line-height: 1;
  }
  .promo-sub {
    font-family: "Cinzel", Georgia, serif;
    font-weight: 400;
    font-size: 19px;
    letter-spacing: 4px;
    margin-top: 4px;
  }
  .promo-offer {
    margin-top: 14px;
    font-size: 17px;
    line-height: 1.3;
    color: var(--ink-soft);
  }

  /* Contact side */
  .card-contact { top: 505px; background: var(--white); }
  .contact-shape { position: absolute; inset: 0; }
  .brand {
    position: absolute;
    left: 40px; top: 175px;
    width: 290px;
    text-align: center;
    color: var(--teal);
    font-family: "Cinzel", Georgia, serif;
    font-weight: 600;
  }
  .brand-name { font-size: 52px; letter-spacing: 2px; line-height: 1; }
  .brand-sub { font-size: 15px; letter-spacing: 3px; margin-top: 6px; }
  .portrait {
    position: absolute;
    right: 28px; top: 22px;
    width: 200px; height: 140px;
    border-radius: 12px;
    background: linear-gradient(135deg, #3f5a3a 0%, #6c6258 55%, #d9d2cb 100%);
  }
  .contact-info {
    position: absolute;
    right: 28px; top: 180px;
    text-align: right;
    color: var(--white);
  }
  .contact-name {
    font-family: "Cinzel", Georgia, serif;
    font-size: 22px;
    letter-spacing: 1.5px;
    font-weight: 400;
  }
  .contact-role { font-size: 16px; line-height: 1.35; }
  .contact-lines { margin-top: 8px; list-style: none; font-size: 15px; line-height: 1.55; }
  .contact-lines li { display: flex; justify-content: flex-end; align-items: center; gap: 8px; }
  .contact-lines svg { width: 14px; height: 14px; fill: var(--white); flex: none; }
</style>
</head>
<body>

<section class="card card-promo">
  <div class="promo-texture" role="img" aria-label="Teal background with a subtle repeating decorative pattern"></div>
  <div class="promo-content">
    <h1 class="promo-name">VENTRINO</h1>
    <p class="promo-sub">REAL ESTATE SERVICES</p>
    <p class="promo-offer">Home owners, call today to receive a<br>FREE market analysis for your homes value!</p>
  </div>
</section>

<section class="card card-contact">
  <svg class="contact-shape" viewBox="0 0 700 400" preserveAspectRatio="none" aria-hidden="true">
    <defs>
      <linearGradient id="panelTeal" x1="0" y1="0" x2="1" y2="1">
        <stop offset="0" stop-color="#2aa9b1"/>
        <stop offset="1" stop-color="#137780"/>
      </linearGradient>
      <linearGradient id="silverBand" x1="0" y1="0" x2="0" y2="1">
        <stop offset="0" stop-color="#f2f4f5"/>
        <stop offset="0.5" stop-color="#8b9296"/>
        <stop offset="1" stop-color="#d6dadc"/>
      </linearGradient>
    </defs>
    <path d="M300 0 H700 V400 H360 C420 300 420 110 300 0 Z" fill="url(#panelTeal)"/>
    <path d="M300 0 C420 110 420 300 360 400 L352 400 C408 300 404 120 290 0 Z" fill="url(#silverBand)"/>
  </svg>

  <div class="brand">
    <div class="brand-name">VENTRINO</div>
    <div class="brand-sub">REAL ESTATE SERVICES</div>
  </div>

  <div class="portrait" role="img" aria-label="Portrait photo of the broker outdoors"></div>

  <div class="contact-info">
    <h2 class="contact-name">CARLA VENTRINO</h2>
    <p class="contact-role">Owner &amp; Qualifying Broker<br>Ventrino Real Estate Services</p>
    <ul class="contact-lines">
      <li>505.718.2094
        <svg viewBox="0 0 24 24"><path d="M6.6 10.8a15 15 0 0 0 6.6 6.6l2.2-2.2a1 1 0 0 1 1-.25 11.4 11.4 0 0 0 3.6.57 1 1 0 0 1 1 1V20a1 1 0 0 1-1 1A17 17 0 0 1 3 4a1 1 0 0 1 1-1h3.5a1 1 0 0 1 1 1c0 1.25.2 2.45.57 3.57a1 1 0 0 1-.25 1z"/></svg>
      </li>
      <li>carla@ventrinohomes.example
        <svg viewBox="0 0 24 24"><path d="M2 5h20v14H2z M4 7v.5l8 5 8-5V7l-8 5z" fill-rule="evenodd"/></svg>
      </li>
      <li>www.ventrinohomes.example
        <svg viewBox="0 0 24 24"><path d="M12 2a10 10 0 1 0 0 20 10 10 0 0 0 0-20zm0 2a8 8 0 0 1 7.7 6H15a13 13 0 0 0-2-5.9A8 8 0 0 1 12 4zm-2.9.6A13 13 0 0 0 7 10H4.3a8 8 0 0 1 4.8-5.4zM4.3 14H7a13 13 0 0 0 2.1 5.4A8 8 0 0 1 4.3 14zm5.1 0h5.2a11 11 0 0 1-2.6 5.6A11 11 0 0 1 9.4 14zm0-4a11 11 0 0 1 2.6-5.6A11 11 0 0 1 14.6 10zm5.5 9.4A13 13 0 0 0 17 14h2.7a8 8 0 0 1-4.8 5.4z"/></svg>
      </li>
    </ul>
  </div>
</section>

</body>
</html>
```